Web Design Project

Please take a look at my current aged website www.talvikhrconsulting.com and my newly designed logo and business cards. I would like a new fresh updated look to my website and my new designs incorporated.
Updates

  Good Morning Everyone

Due to an Austrralian licencing issue I have had to have my logo slightly redesigned.

Would you please be able to look at the newly uploaded files and revise your designs.

Thanks so much.  I am very happy with the calibre and quality of the designs so far.

kind Regards

Marla

Industry/Entity Type

Business

Requirements
Must have
• the exisiting pages and fresh new graphics and a real commitment to my palette of lime green, turqouise and black.

```html
<!DOCTYPE html>
<html lang="en">
<head>
<meta charset="utf-8">
<title>Talvik HR Consulting</title>
<link rel="stylesheet" href="https://fonts.googleapis.com/css2?family=Cardo:ital,wght@0,400;0,700;1,700&family=Sorts+Mill+Goudy:ital@0;1&family=Ubuntu:wght@400;500&display=swap">
<style>
:root{
  --ink:#221f20;
  --turquoise:#1aa6c8;
  --lime:#5aa84f;
  --lime-dark:#3f6f38;
  --panel:#a7a9aa;
  --card:#c1c1c1;
  --text:#1f1d1e;
  --white:#ffffff;
  --orange:#ff8a00;
  --orange-deep:#ff3a00;
}
*{box-sizing:border-box;margin:0;padding:0}
html,body{width:1200px;height:1176px;overflow:hidden;background:var(--white)}
body{position:relative;font-family:"Sorts Mill Goudy",Georgia,serif;color:var(--text)}
.header{position:absolute;left:144px;top:48px;width:912px;height:166px;background:var(--ink);border-radius:8px 8px 4px 4px;box-shadow:0 2px 3px rgba(0,0,0,.35)}
.brand{position:absolute;left:178px;top:84px;display:flex;align-items:center;gap:18px}
.brand-dot{width:106px;height:106px;border-radius:50%;background:var(--turquoise)}
.brand-name{font-family:"Ubuntu",sans-serif;font-weight:500;font-size:43px;color:var(--turquoise);letter-spacing:-.5px;line-height:1}
.brand-tag{font-family:"Ubuntu",sans-serif;font-size:11.5px;color:var(--turquoise);margin-top:4px}
.social{position:absolute;top:32px;left:692px;display:flex;gap:30px}
.social span{width:72px;height:72px;border-radius:50%;box-shadow:0 4px 5px rgba(0,0,0,.3)}
.social span:nth-child(odd){background:var(--turquoise)}
.social span:nth-child(even){background:var(--lime)}
.search{position:absolute;left:684px;top:134px;width:350px;height:41px;border-radius:9px;background:#b9b9b9;border:1px solid #e4e4e4}
.search label{position:absolute;left:14px;top:7px;font-family:"Cardo",serif;font-weight:700;font-size:21px;color:#8a8a8a}
.search .field{position:absolute;left:100px;top:1px;right:1px;bottom:1px;background:var(--ink);border-radius:8px;border:1px solid #777}
.search .field::after{content:"";position:absolute;left:20px;top:8px;width:2px;height:22px;background:var(--white)}
.nav-band{position:absolute;left:96px;top:223px;width:1008px;height:53px;background:var(--lime);border-radius:6px;box-shadow:0 2px 3px rgba(0,0,0,.4)}
.nav{position:absolute;left:144px;top:222px;height:56px;display:flex;list-style:none}
.nav li{height:56px;display:flex;align-items:center;justify-content:center;font-family:"Cardo",serif;font-weight:700;font-size:30px;color:#1e2a1c;background:linear-gradient(#5f9c55,#3f7a38);border:1px solid #2b4c27;border-radius:8px;box-shadow:inset 0 1px 0 rgba(255,255,255,.3)}
.nav li.active{background:var(--turquoise);color:#12303a}
.content{position:absolute;left:144px;top:290px;width:912px;height:752px;background:var(--panel);border-radius:9px;border:1px solid #666;box-shadow:0 2px 3px rgba(0,0,0,.35)}
.intro{position:absolute;left:157px;top:316px;width:486px;height:710px;background:var(--card);border:1px solid #333;border-radius:9px;text-align:center;padding:4px 10px}
.intro h1{font-family:"Cardo",serif;font-style:italic;font-weight:700;font-size:24px;margin-bottom:2px}
.intro p{font-size:20.5px;line-height:29px;margin-bottom:29px}
.intro a{color:var(--turquoise);text-decoration:underline}
.quote{position:absolute;left:660px;top:317px;width:382px;height:237px;background:var(--ink);border:1px solid #888;border-radius:9px;color:var(--white);text-align:center;font-family:"Cardo",serif;font-weight:700;font-size:15.6px;line-height:16.8px;padding:12px 12px}
.quote cite{display:block;margin-top:18px;font-style:normal;font-size:16.5px;line-height:17px}
.media{position:absolute;left:707px;top:580px;width:300px;height:300px;background:#000}
.media .frame{position:absolute;left:0;top:46px;width:300px;height:195px;background:#5b5b5b}
.media .photo{position:absolute;left:9px;top:10px;width:281px;height:176px;background:linear-gradient(#e8e8e8 0,#d6d6d6 55%,#5b4a3e 56%,#f1f1f1 100%)}
.footer{position:absolute;left:144px;top:1056px;width:421px;height:120px;background:var(--ink);border-radius:8px 8px 0 0;text-align:center}
.footer .copy{font-family:"Ubuntu",sans-serif;font-size:15px;color:var(--white);margin-top:12px}
.footer-links{position:absolute;left:54px;top:68px;font-family:"Ubuntu",sans-serif;font-size:15.5px;color:var(--white);letter-spacing:-.3px}
.footer-links a{color:var(--turquoise);text-decoration:none}
.testimonials{position:absolute;left:565px;top:1048px;width:495px;height:128px;border-radius:9px 9px 0 0;overflow:hidden;background:linear-gradient(100deg,var(--orange) 0%,#ff6a00 60%,var(--orange-deep) 100%)}
.testimonials h2{position:absolute;left:51px;top:33px;font-family:"Ubuntu",sans-serif;font-weight:400;font-size:31px;line-height:29px;color:var(--white);letter-spacing:-1px}
.testimonials p{position:absolute;left:51px;top:100px;font-family:"Ubuntu",sans-serif;font-size:13px;color:var(--white)}
.testimonials svg{position:absolute;left:0;top:0}
</style>
</head>
<body>
<header class="header"></header>
<div class="brand">
  <span class="brand-dot"></span>
  <div>
    <div class="brand-name">Talvik HR Consulting</div>
    <div class="brand-tag">Human Resources and Recruitment Solutions</div>
  </div>
</div>
<div class="social" aria-label="Social links"><span></span><span></span><span></span><span></span></div>
<div class="search"><label>Search:</label><div class="field"></div></div>

<div class="nav-band"></div>
<ul class="nav">
  <li class="active" style="width:144px">Home</li>
  <li style="width:206px">Our Services</li>
  <li style="width:244px">Our Consultants</li>
  <li style="width:146px">Our Fees</li>
  <li style="width:172px">Contact Us</li>
</ul>

<main class="content"></main>
<section class="intro">
  <h1>What can Talvik HR Consulting do for me?</h1>
  <p>During these challenging economic times it can be difficult to justify internal human resources management services or support. However as a business owner or Manager you may find that HR support or advice is required from time to time.</p>
  <p>Talvik HR Consulting are an outsourced HR function. We can provide you with that ongoing support, offer solutions and assist you with developing strategies that fit your business and deliver results.</p>
  <p>Take a look at <a href="#">Our Services</a> to see how our comprehensive consultancy can add value to your business.</p>
  <p>By outsourcing some or all of your HR function you will effectively manage your costs, be able to focus on your core business and still have access to professional up-to-date HR advice, systems and processes.</p>
</section>

<blockquote class="quote">“According to a recent survey by Harlow Whitcombe Partners more than 80% of companies outsource some type of task or project each year. The survey concludes that “by farming out management of operations that are not mission-critical, (these companies) are better able to concentrate on growth, competitors and profitability. If you’re not doing any outsourcing, you might be hurting your business”.
  <cite>Source: The Practical Guide to Successful Outsourcing (Dale Fenwick) 2005</cite>
</blockquote>

<div class="media"><div class="frame"><div class="photo" role="img" aria-label="Photo of a businesswoman in a brown jacket with hands folded on a white desk"></div></div></div>

<footer class="footer">
  <div class="copy">Copyright 2012 Talvik HR Consulting</div>
  <nav class="footer-links"><a href="#">Home</a>|<a href="#">Services</a>|<a href="#">Consultants</a>|<a href="#">Fees</a>|<a href="#">Contact Us</a></nav>
</footer>

<aside class="testimonials">
  <svg width="495" height="128" viewBox="0 0 495 128">
    <polygon points="350,128 420,0 470,0 400,128" fill="#2f7a35"/>
    <polygon points="360,128 426,0 462,0 394,128" fill="var(--lime)"/>
    <text x="0" y="0" transform="translate(392,118) rotate(-62)" font-family="Ubuntu, sans-serif" font-size="15" fill="#fff" letter-spacing="1">TESTIMONIALS</text>
  </svg>
  <h2>Testimonials and<br>CV Referees</h2>
  <p>Availiable among request</p>
</aside>
</body>
</html>
```